Volbrey Inc Business Card

Looking to get an updated business card for a Contract Machining company (www.volbreyinc.example) - looking for a clean design the portrays the technical nature of the business - colors can follow the website design and be in any combination that makes sense (red black, white, metallic or silver) - logos attached for use also. Would like space for: Name, title, business phone (555 214-3086), cell phone , website (www.volbreyinc.example) - possibly QR code could be integrated for website (designer choice), business address - 418 Harlow Bend, Alder Falls, ST 48199 (cards will be for 4 employees, I will either need to modify a template or I can provide individual information)
Target Market(s)
Aerospace, defense and medical device manufacturing companies that need machining
Industry/Entity Type
Machining for aerospace, defense, medical
Contact Information for Business Card
Name, Title, Business Phone, Cell Phone, email, business website and business address
Look and feel

```html
<!DOCTYPE html>
<html lang="en">
<head>
<meta charset="UTF-8">
<title>Volbrey Inc Business Card</title>
<link href="https://fonts.googleapis.com/css2?family=Montserrat:wght@400;500;700;800&display=swap" rel="stylesheet">
<style>
  :root {
    --brand-red: #b01c22;
    --ink: #1a1a1a;
    --text-grey: #555555;
    --paper: #ffffff;
    --stage: #3a3a3a;
    --stage-dark: #1e1e1e;
    --back-black: #141414;
  }
  * { margin: 0; padding: 0; box-sizing: border-box; }
  html, body { width: 1200px; height: 900px; overflow: hidden; }
  body {
    background: radial-gradient(ellipse at 50% 40%, var(--stage), var(--stage-dark));
    font-family: 'Montserrat', sans-serif;
    display: flex;
    flex-direction: column;
    align-items: center;
    justify-content: center;
    gap: 60px;
  }
  .card {
    position: relative;
    width: 560px;
    height: 320px;
    border-radius: 3px;
    overflow: hidden;
    box-shadow: 0 0 0 3px var(--brand-red), 0 14px 30px rgba(0,0,0,.5);
  }

  /* front */
  .card-front { background: var(--paper); }
  .edge-strip {
    position: absolute; left: 0; top: 0; bottom: 0; width: 24px;
    background: var(--paper);
    border-right: 3px solid var(--ink);
  }
  .side-band {
    position: absolute; left: 27px; top: 0; bottom: 0; width: 64px;
    background: var(--brand-red);
    border-right: 3px solid var(--ink);
  }
  .logo-disc {
    position: absolute; left: 52px; top: 22px;
    width: 84px; height: 84px; border-radius: 50%;
    background: var(--brand-red);
    border: 4px solid var(--paper);
    box-shadow: 0 0 0 2px var(--brand-red);
  }
  .wordmark {
    position: absolute; left: 150px; top: 34px;
    color: var(--brand-red);
  }
  .wordmark-name {
    font-weight: 800; font-size: 62px; letter-spacing: 1px; line-height: 1;
  }
  .wordmark-suffix {
    font-weight: 400; font-size: 22px; letter-spacing: 1px;
    margin-left: 32px; margin-top: 2px;
  }
  .person {
    position: absolute; right: 34px; top: 160px; text-align: right;
  }
  .person-name {
    color: var(--brand-red); font-weight: 700; font-size: 19px; letter-spacing: .5px;
  }
  .person-title {
    color: var(--text-grey); font-weight: 500; font-size: 13px; letter-spacing: 1px; margin-top: 2px;
  }
  .divider {
    position: absolute; left: 112px; right: 30px; top: 212px;
    height: 1.5px; background: var(--brand-red);
  }
  .contact-list {
    position: absolute; left: 112px; top: 222px;
    list-style: none;
    color: var(--text-grey); font-size: 12.5px; line-height: 20px;
  }
  .contact-list li { display: flex; align-items: center; gap: 7px; }
  .contact-list svg { width: 10px; height: 10px; fill: var(--brand-red); }
  .address {
    position: absolute; right: 34px; bottom: 26px; text-align: right;
    color: var(--text-grey); font-size: 14px; line-height: 20px;
  }

  /* back */
  .card-back { background: var(--back-black); }
  .back-texture {
    position: absolute; inset: 0;
    background: linear-gradient(135deg, #242424 0%, #0f0f0f 55%, #1c1c1c 100%);
  }
  .back-wordmark {
    position: absolute; left: 0; right: 0; top: 50%;
    transform: translateY(-50%);
    text-align: center;
    color: var(--brand-red); font-weight: 800; font-size: 50px; letter-spacing: 1px;
  }
</style>
</head>
<body>

  <section class="card card-front" aria-label="Business card front">
    <div class="edge-strip"></div>
    <div class="side-band"></div>
    <div class="logo-disc"></div>
    <div class="wordmark">
      <div class="wordmark-name">VOLBREY</div>
      <div class="wordmark-suffix">INC.</div>
    </div>
    <div class="person">
      <div class="person-name">DANIEL HARPER</div>
      <div class="person-title">DIRECTOR</div>
    </div>
    <div class="divider"></div>
    <ul class="contact-list">
      <li><svg viewBox="0 0 10 10"><path d="M2 0h2l1 3-1.5 1a6 6 0 0 0 2.5 2.5L7 5l3 1v2a2 2 0 0 1-2 2A8 8 0 0 1 0 2a2 2 0 0 1 2-2z"/></svg>555 214-3086</li>
      <li><svg viewBox="0 0 10 10"><rect x="2" y="0" width="6" height="10" rx="1"/></svg>555-738-4410</li>
      <li><svg viewBox="0 0 10 10"><path d="M0 1.5h10v7H0z M0 1.5l5 4 5-4" stroke="#fff" stroke-width=".8"/></svg>info@volbreyinc.example</li>
      <li><svg viewBox="0 0 10 10"><circle cx="5" cy="5" r="5"/></svg>www.volbreyinc.example</li>
    </ul>
    <div class="address">418 Harlow Bend,<br>Alder Falls, ST 48199</div>
  </section>

  <section class="card card-back" aria-label="Business card back">
    <div class="back-texture" role="img" aria-label="Dark glossy repeating brand pattern across the card back"></div>
    <div class="back-wordmark">VOLBREY</div>
  </section>

</body>
</html>
```